Copper lark buildworks

Copper lark buildworks is a small construction company.
Who is a licenced builder, Carpenter, joiner,
working on heritage ,new build, speacial projects and sometimes furniture

Industry/Entity Type

Construction

```html
<!DOCTYPE html>
<html lang="en">
<head>
<meta charset="utf-8">
<title>Copper lark buildworks – Business Card</title>
<link rel="stylesheet" href="https://fonts.googleapis.com/css2?family=Ubuntu:wght@400;500&family=Lato:wght@400&display=swap">
<style>
  :root {
    --backdrop: #e9e7e3;
    --card: #ffffff;
    --brand-green: #8cc63f;
    --ink: #1b1b1b;
    --text: #222222;
    --divider: #8cc63f;
  }
  * { margin: 0; padding: 0; box-sizing: border-box; }
  html, body {
    width: 1200px;
    height: 902px;
    overflow: hidden;
    background: var(--backdrop);
  }
  .canvas {
    position: relative;
    width: 1200px;
    height: 902px;
  }
  .business-card {
    position: absolute;
    left: 100px;
    top: 165px;
    width: 1000px;
    height: 571px;
    background: var(--card);
    border-radius: 22px;
    overflow: hidden;
    box-shadow: 0 6px 24px rgba(0,0,0,0.12);
  }
  .brand-block {
    position: absolute;
    left: 0;
    top: 160px;
    width: 474px;
    height: 200px;
    display: flex;
    align-items: center;
    justify-content: center;
  }
  .brand-name {
    font-family: "Ubuntu", sans-serif;
    font-weight: 400;
    font-size: 32px;
    color: var(--ink);
    letter-spacing: 0.2px;
  }
  .divider {
    position: absolute;
    left: 474px;
    top: 176px;
    width: 2px;
    height: 178px;
    background: var(--divider);
  }
  .contact-block {
    position: absolute;
    left: 551px;
    top: 170px;
  }
  .person-name {
    font-family: "Ubuntu", sans-serif;
    font-weight: 400;
    font-size: 29px;
    color: var(--ink);
    line-height: 1.1;
  }
  .person-name .surname { color: var(--brand-green); }
  .person-title {
    font-family: "Ubuntu", sans-serif;
    font-size: 22px;
    color: var(--ink);
    margin-top: 2px;
  }
  .contact-list {
    list-style: none;
    margin-top: 24px;
  }
  .contact-item {
    display: flex;
    align-items: center;
    height: 36px;
    font-family: "Lato", sans-serif;
    font-size: 23px;
    color: var(--text);
  }
  .contact-icon {
    width: 28px;
    height: 28px;
    margin-right: 10px;
    flex: none;
  }
  .wave {
    position: absolute;
    left: 0;
    bottom: 0;
    width: 1000px;
    height: 571px;
  }
</style>
</head>
<body>
<div class="canvas">
  <div class="business-card">
    <svg class="wave" viewBox="0 0 1000 571" preserveAspectRatio="none" aria-hidden="true">
      <path d="M0 452 C 150 500, 300 530, 470 518 C 650 505, 820 460, 1000 442 L1000 571 L0 571 Z" fill="var(--brand-green)"/>
      <path d="M0 441 C 160 500, 320 530, 480 520 C 650 508, 830 445, 1000 426 C 830 432, 660 478, 480 496 C 320 510, 160 490, 0 441 Z" fill="var(--ink)"/>
    </svg>

    <div class="brand-block">
      <span class="brand-name">Copper lark buildworks</span>
    </div>

    <div class="divider"></div>

    <div class="contact-block">
      <p class="person-name">Marcus <span class="surname">Hale</span></p>
      <p class="person-title">President</p>
      <ul class="contact-list">
        <li class="contact-item">
          <svg class="contact-icon" viewBox="0 0 28 28" aria-hidden="true">
            <circle cx="14" cy="14" r="12.5" fill="none" stroke="var(--brand-green)" stroke-width="2"/>
            <rect x="10" y="7" width="8" height="14" rx="1.5" fill="none" stroke="var(--brand-green)" stroke-width="1.8"/>
            <line x1="12.5" y1="18.5" x2="15.5" y2="18.5" stroke="var(--brand-green)" stroke-width="1.5"/>
          </svg>
          <span>0431762905</span>
        </li>
        <li class="contact-item">
          <svg class="contact-icon" viewBox="0 0 28 28" aria-hidden="true">
            <circle cx="14" cy="14" r="12.5" fill="none" stroke="var(--brand-green)" stroke-width="2"/>
            <rect x="7.5" y="9.5" width="13" height="9" fill="var(--brand-green)"/>
            <polyline points="7.5,9.5 14,15 20.5,9.5" fill="none" stroke="#fff" stroke-width="1.4"/>
          </svg>
          <span>info@copperlarkbuild.com</span>
        </li>
        <li class="contact-item">
          <svg class="contact-icon" viewBox="0 0 28 28" aria-hidden="true">
            <circle cx="14" cy="14" r="12.5" fill="none" stroke="var(--brand-green)" stroke-width="2"/>
            <circle cx="14" cy="14" r="7" fill="none" stroke="var(--brand-green)" stroke-width="1.5"/>
            <ellipse cx="14" cy="14" rx="3" ry="7" fill="none" stroke="var(--brand-green)" stroke-width="1.2"/>
            <line x1="7" y1="14" x2="21" y2="14" stroke="var(--brand-green)" stroke-width="1.2"/>
          </svg>
          <span>www.copperlarkbuild.com</span>
        </li>
      </ul>
    </div>
  </div>
</div>
</body>
</html>
```